Website and Logo Design for new niche job board.

Hello, We are an up and coming job board that is focused on LEGITIMATE companies that hire telecommuters to work from home. We are looking to build a highly interactive job board and forum/blog. The site is called TaskHarbor.com We focus on helping work at home moms, older workers and college students in work at home positions. We offer free job posting and advertising to the employer and free resume posting to the job seeker. (Free everything basically) Our revenue will be based from banner ads on the site so we will need a space on both sides of the page for those ads. 

The software we are using to build the job board part of the site can be viewed at www.plinkforge.example. It is already built! We do not need job software but a dashboard look to our main page - PLEASE pay attention to this! Do not submit a job board look as we have the job board page built!

These are the sites I like - please use these links to understand exactly the look I want

 

http://www.brightmuffins.example/

http://www.evagrant.example/

http://www.ladiesatwork.example/

https://www.findingnannies.example/index.asp?
Updates

Hi everyone- I think there might be some confusion to what we are looking for. We have the job board software through www.plinkforge.example, we are looking for the main page to be built around that. Basically we want a dashboard look with lots of little boxes to add content such as different articles,podcasts, forums,blogs,highlight different companies hiring,etc. If you can add scrolling or moving objects would be ideal. The less of a static website the better. You dont have to worry about the jobboard portion just the main page when you click on www.TaskHarbor.com, we really need it to capture peoples attention and see its a staffing firm AND a job board, forum, etc for work at home positions.  Here are some looks I am aiming for -

http://www.evagrant.example/

Please use alot of color- lime green, oranges, turquiose blue, purple, lots and lots of color please! I like more tropical colors. Thanks! I dont like red and dark colors at all. Thanks

Target Market(s)

Target customers will be both companies and individuals. The individuals will be a broad age range that are interested in working from home. The companies will be small to large corporations that have valid work from home positions.

Requirements
Must have
• I want a colorful site with moving objects and scrolling text - static sites are bland, and outdated- I am looking for a HIGHLY interactive board. Please do not just throw a template up there and expect me to like it. I am picky and want an ultra sleek design and eye catching. I can make an out of the box website myself, I have 3 other companies and did that -  PLEASE PLEASE DO NOT SHOW ME A COOKIE!
Nice to have
• Would be very nice to have the HTML sliced up for finished designs.
Should not have
• just not boring and static. Anything new and creative is where we are heading.

```html
<!DOCTYPE html>
<html lang="en">
<head>
<meta charset="utf-8">
<title>TaskHarbor.com – Work From Home Jobs</title>
<link href="https://fonts.googleapis.com/css2?family=Ubuntu:wght@400;500;700&family=Open+Sans:wght@400;600;700&family=Roboto+Slab:wght@700&display=swap" rel="stylesheet">
<style>
:root{
  --lime:#9be21c;
  --lime-bright:#c4f524;
  --pink:#e3147b;
  --magenta:#d0116e;
  --orange:#ff6a00;
  --purple:#8a0fa8;
  --turquoise:#3fb4cf;
  --sky:#42b8dc;
  --grey:#676767;
  --ink:#111;
  --white:#fff;
  --yellow:#ffe100;
}
*{box-sizing:border-box;margin:0;padding:0}
html,body{width:892px;height:1200px;overflow:hidden;background:var(--white)}
body{position:relative;font-family:"Open Sans",sans-serif;color:var(--ink);font-size:8px}
.abs{position:absolute}
.heading{font-family:"Ubuntu",sans-serif}

/* top utility bar */
.utility-bar{left:0;top:0;width:892px;height:18px;background:linear-gradient(var(--lime-bright),var(--lime));}
.utility-links{right:104px;top:4px;font-weight:700;font-size:8px;letter-spacing:.3px}
.utility-links span{margin:0 3px}

/* header */
.brand{left:102px;top:34px;display:flex;align-items:center;gap:8px}
.brand-dot{width:52px;height:52px;border-radius:50%;background:var(--pink)}
.brand-name{font-family:"Ubuntu",sans-serif;font-weight:700;font-size:25px;color:var(--pink)}
.promo-top{left:424px;top:30px;width:365px;height:70px;background:linear-gradient(90deg,#2a2a2a 0%,#4a1c1c 60%,#7a2a2a 100%);
  color:var(--white);font-family:"Ubuntu",sans-serif;font-weight:700;font-size:24px;line-height:31px;padding:2px 6px}

/* navigation */
.main-nav{left:0;top:108px;width:892px;height:28px;background:var(--pink)}
.nav-item{top:7px;color:var(--white);font-family:"Ubuntu",sans-serif;font-weight:500;font-size:10px}
.nav-home{left:119px;top:3px;width:63px;height:20px;background:var(--lime);color:var(--ink);text-align:center;line-height:20px;border-radius:2px}
.sub-strip{left:0;top:136px;width:892px;height:23px;background:linear-gradient(#fff,#e7e7e7)}

/* hero */
.hero{left:0;top:159px;width:892px;height:234px;background:linear-gradient(160deg,#49c0db,#2fa2c0 60%,#3bb3cf)}
.section-title{font-family:"Ubuntu",sans-serif;font-weight:500;font-size:13px;color:var(--white)}
.search-panel{left:102px;top:196px;width:348px;height:184px;border-radius:9px;background:linear-gradient(#a7ec4a,#92e41c);box-shadow:-5px 5px 0 #6d8a6f}
.field-label{font-size:8px;font-weight:700;left:15px}
.field{left:15px;width:179px;height:19px;background:var(--white);border:1px solid #6a9f26;font-size:7.5px;color:#888;padding:4px 5px}
.search-btn{left:76px;top:147px;width:51px;height:16px;background:var(--pink);color:var(--white);font-size:8px;font-weight:600;text-align:center;line-height:16px}
.search-quote{left:218px;top:59px;width:112px;text-align:center;font-family:"Ubuntu",sans-serif;font-weight:700;font-size:12px;line-height:15px}
.advanced{left:231px;top:150px;font-size:8px;font-weight:700;display:flex;align-items:center;gap:4px}

.featured-card{left:544px;top:194px;width:240px;height:184px;background:var(--white);border-radius:8px;box-shadow:-4px 4px 0 #8d9aa0}
.featured-badge{left:19px;top:14px;width:60px;height:60px;border-radius:6px;border:3px solid #d51b1b;background:#fff}
.featured-name{left:98px;top:20px;font-size:9px;font-weight:600}
.featured-copy{left:98px;top:38px;width:132px;font-size:7.5px;line-height:9px}
.read-more{font-weight:700;font-size:7.5px}
.other-label{left:15px;top:124px;font-size:8.5px;font-weight:600}
.employer-name{top:146px;font-family:"Ubuntu",sans-serif;font-weight:700;font-size:19px;color:#333}

/* latest jobs */
.latest-title{left:100px;top:417px;font-family:"Ubuntu",sans-serif;font-weight:500;font-size:13px}
.jobs-panel{left:102px;top:444px;width:417px;height:305px;background:var(--white);border:1px solid #ccc;border-radius:9px;box-shadow:5px 3px 0 #999}
.tab{top:10px;height:17px;line-height:17px;text-align:center;color:var(--white);font-size:8px;font-weight:600;background:var(--ink)}
.tab-active{background:var(--sky)}
.more-jobs{right:12px;top:15px;font-size:7px;font-weight:700;letter-spacing:.4px}
.job-table{left:12px;top:29px;width:393px;border-collapse:collapse;font-size:8px;background:#f5f5f5}
.job-table td{height:42.3px;border-bottom:1px solid #d8d8d8;vertical-align:middle;padding-left:10px}
.job-table .job-desc{font-size:7px;line-height:8.5px}
.job-table .job-desc b{font-size:8px}

/* feature tiles */
.tile{left:545px;width:244px;height:90px;border-radius:4px;color:var(--white);box-shadow:2px -4px 0 #777}
.tile-blog{top:443px;background:linear-gradient(#ee3c96,var(--magenta))}
.tile-article{top:549px;background:linear-gradient(#ff8a1e,var(--orange))}
.tile-podcast{top:655px;background:linear-gradient(#a61ac4,var(--purple))}
.tile-title{left:14px;font-family:"Ubuntu",sans-serif;font-weight:500;font-size:17px}
.tile-copy{left:14px;font-size:7.5px;font-weight:700;line-height:9.2px;width:136px}
.tile-art{border-radius:8px}

/* info boxes */
.info-box{top:765px;height:139px;background:var(--grey);color:var(--white)}
.info-head{left:0;top:0;width:100%;height:26px;font-family:"Ubuntu",sans-serif;font-weight:500;font-size:12.5px;color:var(--ink);padding:6px 10px}
.head-yellow{background:linear-gradient(170deg,var(--yellow) 60%,var(--turquoise) 61%)}
.head-pink{background:linear-gradient(170deg,#b0128a 60%,var(--pink) 61%);color:var(--white)}
.info-list{left:10px;top:32px;list-style:none;font-size:8px;font-weight:600;line-height:12.7px;letter-spacing:.3px}
.info-list li::before{content:"-";margin-right:9px}
.scrollbar{right:1px;top:27px;width:11px;height:111px;background:#eee;border-left:1px solid #ccc}
.scroll-thumb{left:1px;top:45px;width:8px;height:26px;background:#cfd8ec;border-radius:2px}
.forum-copy{left:11px;top:37px;width:200px;font-size:8px;font-weight:600;line-height:11.3px;letter-spacing:.2px}

/* ads */
.ad-home{left:102px;top:924px;width:416px;height:78px;background:linear-gradient(180deg,#2c4f86,#7aa9c9 55%,#b9b08e);
  font-family:"Roboto Slab",serif;font-weight:700;font-size:24px;color:var(--white);padding:2px 12px;line-height:36px}
.ad-home small{position:absolute;right:22px;bottom:10px;font-size:11px;color:#333}
.ad-dog{left:102px;top:1015px;width:416px;height:127px;background:#ff9966}
.ad-dog-name{left:10px;top:14px;font-family:"Roboto Slab",serif;font-weight:700;font-size:33px;color:var(--white)}
.ad-dog-copy{left:11px;top:85px;font-size:12px;color:var(--white);line-height:16px}
.ad-dog-photo{left:322px;top:4px;width:88px;height:118px;background:linear-gradient(#9bb07a,#c4b48a);border:4px solid #fff}

/* newsletter */
.newsletter{left:565px;top:913px;width:224px;height:139px;background:var(--grey);color:var(--white)}
.newsletter .info-head{color:var(--white);padding-left:38px;background:linear-gradient(170deg,var(--pink) 60%,var(--yellow) 61%)}
.news-icon{left:8px;top:4px;width:20px;height:18px;background:#dfe9f3;border-radius:2px}
.news-label{left:13px;font-size:8px;font-weight:600}
.news-field{left:13px;width:192px;height:20px;background:var(--white)}
.subscribe{left:59px;top:112px;width:80px;height:18px;border-radius:9px;background:var(--pink);text-align:center;line-height:18px;font-size:8px;font-weight:700}

.social{left:565px;top:1066px;width:224px;height:77px;background:linear-gradient(#55c3e4,#2aa6d6);text-align:center}
.social-label{left:0;top:10px;width:100%;font-size:9px;font-weight:600;color:var(--white)}
.social-btn{top:31px;width:70px;height:33px;line-height:33px;font-size:12px;font-weight:700}

.footer{left:0;top:1175px;width:892px;height:25px;background:linear-gradient(var(--lime-bright),var(--lime));text-align:center;line-height:25px;font-size:8px;font-weight:700}
</style>
</head>
<body>

<div class="abs utility-bar"></div>
<div class="abs utility-links">Login <span>|</span> Register <span>|</span> Contact Us</div>

<header>
  <div class="abs brand"><span class="brand-dot"></span><span class="brand-name">TaskHarbor.com</span></div>
  <div class="abs promo-top" role="img" aria-label="Banner ad with photo of dice">Why Gamble?<br>We’re a Sure Thing!</div>
</header>

<nav class="abs main-nav">
  <div class="abs nav-item nav-home">HOME</div>
  <div class="abs nav-item" style="left:228px">MY ACCOUNT</div>
  <div class="abs nav-item" style="left:359px">FIND JOBS</div>
  <div class="abs nav-item" style="left:471px">POST RESUME</div>
  <div class="abs nav-item" style="left:597px">REGISTER</div>
  <div class="abs nav-item" style="left:703px">EMPLOYER</div>
</nav>
<div class="abs sub-strip"></div>

<section class="abs hero" role="img" aria-label="Turquoise cracked-earth texture background"></section>
<div class="abs section-title" style="left:102px;top:167px">JOB SEARCH</div>
<div class="abs section-title" style="left:544px;top:167px">FEATURED EMPLOYER</div>

<form class="abs search-panel">
  <div class="abs field-label" style="top:22px">Job Title:</div>
  <div class="abs field" style="top:33px">(e.g., nurse)</div>
  <div class="abs field-label" style="top:63px">Skills/Keywords:</div>
  <div class="abs field" style="top:75px">(e.g., healthcare, sales)</div>
  <div class="abs field-label" style="top:105px">Location:</div>
  <div class="abs field" style="top:117px">(city, state, or zip code)</div>
  <div class="abs search-btn">Search</div>
  <div class="abs search-quote">“FIND THE JOB YOU DESERVE MOST”</div>
  <div class="abs advanced">Advance Search
    <svg width="12" height="12" viewBox="0 0 12 12"><circle cx="6" cy="6" r="6" fill="#111"/><path d="M3 4.5h6L6 8z" fill="#fff"/></svg>
  </div>
</form>

<aside class="abs featured-card">
  <div class="abs featured-badge"></div>
  <div class="abs featured-name">Meadowline Assurance</div>
  <p class="abs featured-copy">Lorem Ipsum is simply dummy text of the printing and typesetting industry. Lorem Ipsum has been the industry's standard dummy text ever since the 1500s.<br><span class="read-more" style="display:block;text-align:right;margin-top:3px;margin-right:8px">Read More</span></p>
  <div class="abs other-label">Other Employers</div>
  <div class="abs employer-name" style="left:15px">Velonix</div>
  <div class="abs employer-name" style="left:90px">Orbanet</div>
  <div class="abs employer-name" style="left:168px">Brantel</div>
</aside>

<h2 class="abs latest-title">LATEST JOBS</h2>
<section class="abs jobs-panel">
  <div class="abs tab tab-active" style="left:12px;width:94px">By Area of Interest</div>
  <div class="abs tab" style="left:112px;width:93px">By Field</div>
  <div class="abs tab" style="left:210px;width:93px">By Qualification</div>
  <div class="abs more-jobs">MORE JOBS</div>
  <table class="abs job-table">
    <tr><td style="width:65px">April 05</td><td class="job-desc" style="width:135px"><b>Data Entry</b><br>Lorem Ipsum is simply<br>dummy text of the printing</td><td style="width:58px">Norvane</td><td style="width:67px;font-weight:700">Computer</td><td>$10/Hour</td></tr>
    <tr><td>April 05</td><td class="job-desc"><b>Lorum Ipsum</b><br>Lorem Ipsum is simply<br>dummy text of the printing</td><td>Norvane</td><td style="font-weight:700">Demo</td><td>$10/Hour</td></tr>
    <tr><td>April 05</td><td class="job-desc"><b>Lorum Ipsum</b><br>Lorem Ipsum is simply<br>dummy text of the printing</td><td>Norvane</td><td style="font-weight:700">Demo</td><td>$10/Hour</td></tr>
    <tr><td>April 05</td><td class="job-desc"><b>Lorum Ipsum</b><br>Lorem Ipsum is simply<br>dummy text of the printing</td><td>Norvane</td><td style="font-weight:700">Demo</td><td>$10/Hour</td></tr>
    <tr><td>April 05</td><td class="job-desc"><b>Lorum Ipsum</b><br>Lorem Ipsum is simply<br>dummy text of the printing</td><td>Norvane</td><td style="font-weight:700">Demo</td><td>$10/Hour</td></tr>
    <tr><td>April 05</td><td class="job-desc"><b>Lorum Ipsum</b><br>Lorem Ipsum is simply<br>dummy text of the printing</td><td>Norvane</td><td style="font-weight:700">Demo</td><td>$10/Hour</td></tr>
  </table>
</section>

<article class="abs tile tile-blog">
  <div class="abs tile-title" style="top:8px">Our blog</div>
  <p class="abs tile-copy" style="top:34px">Lorem Ipsum is simply dummy text of the printing and typesetting industry.<br><span style="font-size:7px">Read More</span></p>
  <div class="abs tile-art" style="left:160px;top:6px;width:78px;height:78px;background:#ff8a2a" role="img" aria-label="Blog icon"></div>
</article>
<article class="abs tile tile-article">
  <div class="abs tile-title" style="top:6px">Latest Article</div>
  <p class="abs tile-copy" style="top:31px;width:146px">Mara L.<br>Lorem Ipsum is simply dummy text of the printing and typesetting industry.<br><span style="font-size:7px">Read More</span></p>
  <div class="abs tile-art" style="left:164px;top:6px;width:75px;height:80px;background:linear-gradient(#c7ccd2,#8d8f93)" role="img" aria-label="Portrait photo of the article author"></div>
</article>
<article class="abs tile tile-podcast">
  <div class="abs tile-title" style="top:26px;left:17px;line-height:20px">Listen Live<br>Our Podcasts</div>
  <div class="abs tile-art" style="left:152px;top:6px;width:82px;height:80px;background:radial-gradient(circle,#ff8a1e 35%,#4a3a4a 70%,transparent 72%)" role="img" aria-label="Headphones around a podcast feed icon"></div>
</article>

<section class="abs info-box" style="left:102px;width:218px">
  <div class="abs info-head head-yellow">List of Jobs</div>
  <ul class="abs info-list"><li>Accounts</li><li>Audits</li><li>Computer Software</li><li>Computer Data Entry</li><li>Graphic Designing</li><li>Logo Designing</li><li>S.E.O.</li><li>Web Designing</li></ul>
  <div class="abs scrollbar"><div class="abs scroll-thumb"></div></div>
</section>
<section class="abs info-box" style="left:331px;width:223px">
  <div class="abs info-head head-pink">Task Harbor Forum</div>
  <p class="abs forum-copy">Lorem Ipsum is simply dummy text of the printing and typesetting industry. Lorem Ipsum has been the industry's standard dummy text ever since the 1500s, when an unknown printer took a galley of type and scrambled it to make a type specimen book.<br><span style="display:block;text-align:right;margin-top:3px;margin-right:14px">Read More</span></p>
</section>
<section class="abs info-box" style="left:565px;width:224px">
  <div class="abs info-head head-yellow">Employers List</div>
  <ul class="abs info-list"><li>JS Designs</li><li>Atlantis &amp; Co</li><li>Draft Circle</li><li>Freelance</li><li>Keystone Property Care</li><li>Web Portal</li><li>Online Work Portal</li><li>Global Computers</li></ul>
  <div class="abs scrollbar"><div class="abs scroll-thumb"></div></div>
</section>

<div class="abs ad-home" role="img" aria-label="Banner ad with coastal beach photo">New Home...<br>&nbsp;New Life Style<small>Crestline Townhomes</small></div>
<div class="abs ad-dog">
  <div class="abs ad-dog-name">PawSprint.example</div>
  <div class="abs ad-dog-copy">An Active Dog’s Source For ...<br>Health, Gear, News, Education &amp; Recreation.</div>
  <div class="abs ad-dog-photo" role="img" aria-label="Photo of a dog leaping on grass"></div>
</div>

<section class="abs newsletter">
  <div class="abs info-head">Newsletter</div>
  <div class="abs news-icon" role="img" aria-label="Envelope icon"></div>
  <div class="abs news-label" style="top:33px">Name</div>
  <div class="abs news-field" style="top:44px"></div>
  <div class="abs news-label" style="top:71px">Email</div>
  <div class="abs news-field" style="top:82px"></div>
  <div class="abs subscribe">Subscribe</div>
</section>

<section class="abs social">
  <div class="abs social-label">Find TaskHarbor On:</div>
  <div class="abs social-btn" style="left:18px;background:#2d4f8e;color:#fff">Friendnest</div>
  <div class="abs social-btn" style="left:117px;background:#fff;color:#2aa6d6;border:1px solid #333">Chirply</div>
</section>

<footer class="abs footer">©2010 taskharbor.com - All Rights Reserved</footer>

</body>
</html>
```